Eyecatching website design for commercial lighting business

This contest is all about the graphic design aspect. We need a striking website design for a commercial lighting company. We want something really eye catching to introduce people to our range of induction and LED lights which save businesses money on maintenance and electricity costs.

To be successful in this contest you will need to provide a design and pictures for the pages listed below.

We are using the platform velbrin.com.au and you can see the attached template which everything will be loaded into so we just need HTML files which we can upload and we can do everything else from Velbrin.

The final design should be strong and clean and use the colours and textures in the attached business card file.

Detailed requirements:

Please see attached screenshot of the website template, all we need is a fantastic graphic design and improvement/ incorporation of our logo for the following pages
Page Headings:
1. Home
About Us, Contact Us, snapshot of and link to Blog

Each of the below pages will have several paragraphs of text followed by a list of suitable products which is generated from our product catalogue.

2. Car Park Lighting
3. Educational Lighting
4. Hospitality Lighting
5. Office & Shop Lighting
6. Warehouse Lighting

Some of the website we have seen which are similar in nature are:
http://www.quorvanlamps.com.au/
http://www.tibrox.com/
http://www.gandowlumen.net/commercial-led
but we really want a modern, eye catching and memorable design

Some of the designs built on Velbrin that we like are:

http://www.pemberhollow.com.au/
http://www.marwickgoods.com.au/
http://www.kelmorabay.com.au/

I've also uploaded a couple of photos that we love. We'd like something similar for each industry.

Target Market(s)

Company Owners, Maintenance & Facilities Managers, Electrical Contractors

Industry/Entity Type

Electrical

Coding

Coded - Design and coding required

Number of Pages Required

5+ page

Font styles to use
Sans Serif

Colors
33a6d7
ec1f27

Requirements
Must have
• -Must scale to mobile
• -HTML coded files need to be provided (HTML Bootstrap)
Nice to have
• -Prefer incorporation of our logo into header bar
• -Design of 2-3 advertising banners which can be displayed on the home page
• -Prominent call to action button towards top of page 'Get a quote' or similar
• -Grid based design HTML Bootstrap

```html
<!DOCTYPE html>
<html lang="en">
<head>
<meta charset="utf-8">
<title>Korvel Business Solutions – Commercial Lighting</title>
<link href="https://fonts.googleapis.com/css2?family=Open+Sans:wght@400;600;700&family=Raleway:wght@400;600;700&display=swap" rel="stylesheet">
<style>
:root{
  --blue:#33a6d7;
  --blue-dark:#1f7fae;
  --red:#ec1f27;
  --red-dark:#c9141b;
  --navy:#14253a;
  --ink:#333b44;
  --muted:#7a8590;
  --light:#f1f2f4;
  --footer:#1c1f24;
  --footer-bottom:#121417;
  --white:#ffffff;
}
*{margin:0;padding:0;box-sizing:border-box}
html,body{width:1200px;height:2328px;overflow:hidden}
body{font-family:"Open Sans",Arial,sans-serif;color:var(--ink);background:var(--white);position:relative}
h1,h2,h3,h4{font-family:"Raleway",Arial,sans-serif}

/* header */
.site-header{height:108px;position:relative;background:var(--white)}
.brand{position:absolute;left:180px;top:14px;display:flex;align-items:center;gap:12px}
.brand-mark{width:56px;height:56px;border-radius:50%;background:var(--red)}
.brand-name{font-family:"Raleway",sans-serif;font-weight:700;font-size:22px;line-height:24px;color:var(--navy);letter-spacing:1px}
.call{position:absolute;right:100px;top:34px;text-align:right}
.call small{display:block;font-size:11px;color:var(--muted);letter-spacing:1px}
.call strong{font-size:22px;color:var(--navy)}
.main-nav{height:36px;background:var(--red);display:flex;justify-content:center}
.main-nav a{color:var(--white);text-decoration:none;font-size:13px;font-weight:600;letter-spacing:1px;line-height:36px;padding:0 56px}
.main-nav a.active{background:var(--red-dark)}

/* hero */
.hero{height:516px;position:relative;background:linear-gradient(180deg,#3b4a63 0%,#c9b9a0 45%,#7a6b5a 100%)}
.hero-tag{position:absolute;left:180px;top:196px}
.hero-tag h1{background:var(--blue);color:var(--white);font-size:44px;font-weight:700;padding:4px 22px;display:inline-block}
.hero-tag p{background:rgba(20,37,58,.85);color:var(--white);font-family:"Raleway",sans-serif;font-size:28px;font-weight:600;padding:6px 22px;margin-top:10px;display:inline-block}
.hero-arrow{position:absolute;top:200px;width:30px;height:60px}
.hero-arrow.left{left:118px}.hero-arrow.right{right:118px}

/* solutions */
.solutions{position:absolute;left:200px;top:600px;width:800px;height:240px;background:var(--white);box-shadow:0 4px 16px rgba(0,0,0,.15);text-align:center;padding-top:26px}
.solutions h2{font-size:20px;font-weight:600;letter-spacing:1px;color:var(--ink)}
.solution-grid{display:flex;justify-content:center;gap:18px;margin-top:22px}
.solution-card{width:176px}
.solution-photo{height:104px}
.solution-card span{display:block;background:var(--blue);color:var(--white);font-size:13px;font-weight:600;padding:6px 0}

/* save band */
.save{position:absolute;top:870px;left:0;width:1200px;height:210px;background:linear-gradient(90deg,#3a1f4d,#6a3d7a 50%,#2c1b3e);text-align:center;padding-top:36px}
.save h2{color:var(--white);font-size:44px;font-weight:700;letter-spacing:1px}
.save p{color:#e6dced;font-size:14px;margin-top:8px}
.btn{display:inline-block;background:var(--red);color:var(--white);font-size:13px;font-weight:700;padding:10px 30px;text-decoration:none;margin-top:26px}

/* welcome */
.welcome{position:absolute;top:1112px;left:208px;width:790px;display:flex;justify-content:space-between}
.welcome-text{width:440px}
.welcome-text h2{font-size:23px;font-weight:600;color:var(--navy);line-height:30px;white-space:nowrap}
.welcome-text p{font-size:12px;line-height:19px;color:var(--muted);margin-top:10px}
.welcome-text ul{list-style:none;margin-top:10px}
.welcome-text li{font-size:12px;color:var(--muted);padding-left:20px;position:relative;margin-bottom:6px}
.welcome-text li::before{content:"";position:absolute;left:0;top:4px;width:10px;height:10px;background:var(--blue)}
.video{width:330px;height:200px;position:relative;background:radial-gradient(circle at 40% 50%,#f4ead0,#b48b4a 60%,#5a3d1e)}
.video svg{position:absolute;left:135px;top:70px}

/* divider + products */
.divider{position:absolute;top:1380px;left:0;width:1200px;height:30px}
.products{position:absolute;top:1408px;left:0;width:1200px;height:272px;background:var(--light)}
.product-grid{display:flex;justify-content:center;gap:30px;padding-top:34px}
.product{width:170px;text-align:center}
.product-photo{height:90px;width:90px;margin:0 auto;border-radius:50%;background:radial-gradient(circle,#ffffff,#c9ccd1 75%)}
.product h3{font-size:15px;font-weight:600;margin-top:14px;color:var(--ink)}
.product p{font-size:11px;line-height:16px;color:var(--muted);margin-top:6px}
.btn-small{display:inline-block;border:1px solid #bbb;font-size:10px;padding:4px 14px;margin-top:10px;color:var(--ink);background:var(--white)}

/* blogs */
.blogs{position:absolute;top:1712px;left:0;width:1200px;height:352px;background:var(--blue);text-align:center;padding-top:34px}
.blogs h2{color:var(--white);font-size:30px;font-weight:600;letter-spacing:2px}
.blog-grid{display:flex;justify-content:center;gap:28px;margin-top:30px}
.blog{width:244px;text-align:left}
.blog-photo{height:108px}
.blog h3{font-size:13px;color:var(--white);margin-top:8px;font-weight:700}
.blog p{font-size:11px;line-height:16px;color:#e3f3fb;margin-top:4px}
.blog a{font-size:11px;color:var(--white);display:inline-block;margin-top:6px}

/* footer */
.site-footer{position:absolute;top:2064px;left:0;width:1200px;height:216px;background:var(--footer);display:flex;justify-content:center;gap:70px;padding-top:36px}
.footer-col h4{color:var(--white);font-size:12px;letter-spacing:1px;margin-bottom:10px}
.footer-col a,.footer-col span{display:block;font-size:11px;color:#9aa3ad;line-height:19px;text-decoration:none}
.social{display:flex;gap:8px;margin-top:8px}
.social i{width:14px;height:14px;border-radius:50%;background:#9aa3ad;display:block}
.footer-bottom{position:absolute;top:2280px;left:0;width:1200px;height:48px;background:var(--footer-bottom);font-size:11px;color:#6f7882;line-height:48px;padding-left:208px}
</style>
</head>
<body>

<header class="site-header">
  <div class="brand">
    <div class="brand-mark"></div>
    <div class="brand-name">KORVEL<br>BUSINESS SOLUTIONS</div>
  </div>
  <div class="call"><small>CALL US NOW</small><strong>(03) 9000 4821</strong></div>
</header>
<nav class="main-nav">
  <a class="active" href="#">HOME</a><a href="#">ABOUT US</a><a href="#">PRODUCTS</a><a href="#">BLOG</a><a href="#">CONTACT US</a>
</nav>

<section class="hero" role="img" aria-label="Modern retail interior lit by LED ceiling lights">
  <div class="hero-tag"><h1>LED LIGHTING</h1><br><p>SOLUTIONS &amp; PRODUCTS</p></div>
  <svg class="hero-arrow left" viewBox="0 0 30 60"><polyline points="24,4 6,30 24,56" fill="none" stroke="#fff" stroke-width="4"/></svg>
  <svg class="hero-arrow right" viewBox="0 0 30 60"><polyline points="6,4 24,30 6,56" fill="none" stroke="#fff" stroke-width="4"/></svg>
</section>

<section class="solutions">
  <h2>LIGHTING SOLUTIONS</h2>
  <div class="solution-grid">
    <div class="solution-card"><div class="solution-photo" role="img" aria-label="Lit car park" style="background:linear-gradient(#d9a34a,#6b4a22)"></div><span>Car Park Lighting</span></div>
    <div class="solution-card"><div class="solution-photo" role="img" aria-label="Bright classroom" style="background:linear-gradient(#e9e6da,#9c8f72)"></div><span>Educational Lighting</span></div>
    <div class="solution-card"><div class="solution-photo" role="img" aria-label="LED chips close up" style="background:linear-gradient(#dfe9ef,#7d97a8)"></div><span>Hospitality Lighting</span></div>
    <div class="solution-card"><div class="solution-photo" role="img" aria-label="Office interior with ceiling lights" style="background:linear-gradient(#a8553a,#3e2a24)"></div><span>Office Lighting</span></div>
  </div>
</section>

<section class="save" role="img" aria-label="Warehouse ceiling with high bay lights">
  <h2>SAVE ELECTRICITY &amp; MONEY</h2>
  <p>Switch to modern LED and induction lighting and cut your energy and upkeep costs.</p>
  <a class="btn" href="#">CLICK HERE</a>
</section>

<section class="welcome">
  <div class="welcome-text">
    <h2>Welcome to the Commercial Lighting<br>Division of Korvel Business Solutions</h2>
    <p>We help businesses across Victoria cut energy bills with efficient induction and LED lighting. Our team designs, supplies and installs fittings that last longer and need less upkeep.</p>
    <p>We focus on lower running costs and simple maintenance.</p>
    <ul>
      <li>Commercial lighting design and energy audits</li>
      <li>Quality LED and induction products with full warranty support</li>
    </ul>
  </div>
  <div class="video" role="img" aria-label="Video still of an LED light bulb">
    <svg width="60" height="60" viewBox="0 0 60 60"><circle cx="30" cy="30" r="29" fill="#14253a"/><polygon points="24,18 44,30 24,42" fill="#fff"/></svg>
  </div>
</section>

<svg class="divider" viewBox="0 0 1200 30" preserveAspectRatio="none"><polygon points="0,28 570,28 600,2 630,28 1200,28 1200,30 0,30" fill="#f1f2f4"/></svg>
<section class="products">
  <div class="product-grid">
    <div class="product"><div class="product-photo" role="img" aria-label="LED lamp"></div><h3>Product Name</h3><p>Long life fitting with low power draw and clean light.</p><span class="btn-small">Learn more</span></div>
    <div class="product"><div class="product-photo" role="img" aria-label="LED bulb"></div><h3>Product Name</h3><p>Long life fitting with low power draw and clean light.</p><span class="btn-small">Learn more</span></div>
    <div class="product"><div class="product-photo" role="img" aria-label="LED spotlight"></div><h3>Product Name</h3><p>Long life fitting with low power draw and clean light.</p><span class="btn-small">Learn more</span></div>
    <div class="product"><div class="product-photo" role="img" aria-label="LED corn lamp"></div><h3>Product Name</h3><p>Long life fitting with low power draw and clean light.</p><span class="btn-small">Learn more</span></div>
  </div>
</section>

<section class="blogs">
  <h2>LATEST BLOGS</h2>
  <div class="blog-grid">
    <article class="blog"><div class="blog-photo" role="img" aria-label="Warehouse with ceiling lights" style="background:linear-gradient(#b9d3e6,#4f6f88)"></div><h3>Warehouse retrofit results</h3><p>Short summary of the article with key savings and results for clients.</p><a>Read more</a></article>
    <article class="blog"><div class="blog-photo" role="img" aria-label="School hall interior" style="background:linear-gradient(#e8d3a8,#8a6a3a)"></div><h3>Lower bills for schools</h3><p>Short summary of the article with key savings and results for clients.</p><a>Read more</a></article>
    <article class="blog"><div class="blog-photo" role="img" aria-label="Lit car park structure" style="background:linear-gradient(#d2e0ea,#6d8699)"></div><h3>Car park safety upgrades</h3><p>Short summary of the article with key savings and results for clients.</p><a>Read more</a></article>
  </div>
</section>

<footer class="site-footer">
  <div class="footer-col"><h4>COMPANY</h4><a>About Us</a><a>Blog</a><a>Testimonials</a><a>FAQs</a></div>
  <div class="footer-col"><h4>PRODUCTS</h4><a>LED Panels</a><a>Downlights</a><a>Floodlights</a><a>High Bays</a></div>
  <div class="footer-col"><h4>RESOURCES</h4><a>Case Studies</a><a>Guides</a><a>Rebates</a><a>Careers</a></div>
  <div class="footer-col"><h4>SUPPORT</h4><a>Contact</a><a>Warranty</a><a>Shipping</a><a>Returns</a></div>
  <div class="footer-col"><h4>CONTACT US</h4><span>12 Harlow St, Melbourne VIC 3000</span><span>Phone 03 9000 4821</span><span>info@korvel.com.au</span><div class="social"><i></i><i></i><i></i><i></i></div></div>
</footer>
<div class="footer-bottom">© 2015 Korvel Business Solutions. All rights reserved.</div>

</body>
</html>
```